Folded A4 flyer for design&construction company

Folded A4 flyer needed. Keywords: elegant, stylish
our website www.dorvika.ae

Industry/Entity Type

Construction

```html
<!DOCTYPE html>
<html lang="en">
<head>
<meta charset="utf-8">
<title>Dorvika – Folded Flyer</title>
<link rel="stylesheet" href="https://fonts.googleapis.com/css2?family=Lato:wght@400;700&family=Bebas+Neue&display=swap">
<style>
  :root{
    --bg:#8c8c8c;
    --paper:#ffffff;
    --paper-shade:#e6e6e6;
    --ink:#111111;
    --grey-text:#555555;
    --gold-dark:#8a5a14;
    --gold:#c9962e;
    --gold-light:#f0cf72;
    --blue-line:#1f5fa8;
    --white:#ffffff;
  }
  *{margin:0;padding:0;box-sizing:border-box}
  html,body{width:1200px;height:1200px;overflow:hidden}
  body{background:var(--bg);font-family:"Lato",sans-serif;position:relative}
  .spread{position:absolute;left:40px;top:204px;width:1120px;height:792px;box-shadow:0 10px 30px rgba(0,0,0,.35);overflow:hidden}
  .spread-art{position:absolute;inset:0;display:block}
  .brand-name{position:absolute;font-family:"Lato",sans-serif;font-weight:400;letter-spacing:1px;line-height:1;white-space:nowrap}
  .cover-brand{left:620px;top:58px;font-size:40px;color:var(--ink)}
  .cover-web{position:absolute;right:52px;top:26px;font-size:24px;font-weight:700;color:var(--grey-text);letter-spacing:.5px;white-space:nowrap}
  .cover-headline{position:absolute;left:560px;width:560px;top:580px;text-align:center;font-family:"Bebas Neue",sans-serif;font-weight:400;font-size:52px;letter-spacing:1px;color:var(--gold-light);line-height:1}
  .cover-body{position:absolute;left:610px;width:460px;top:648px;text-align:center;font-size:13px;line-height:1.45;color:var(--white)}
  .back-brand{left:66px;top:652px;font-size:34px;color:var(--white)}
  .back-phone{position:absolute;left:290px;top:652px;font-size:20px;line-height:1;color:var(--white);white-space:nowrap}
  .back-quote{position:absolute;left:290px;top:680px;font-size:10px;line-height:1;color:var(--white);white-space:nowrap}
  .back-email{position:absolute;left:66px;top:716px;font-size:15px;line-height:1;color:var(--white);letter-spacing:.5px}
  .back-address{position:absolute;left:66px;top:750px;font-size:14px;line-height:1;color:var(--white);white-space:nowrap}
</style>
</head>
<body>
<main class="spread">
  <svg class="spread-art" viewBox="0 0 1120 792" xmlns="http://www.w3.org/2000/svg">
    <defs>
      <linearGradient id="paperLeft" x1="0" y1="0" x2="1" y2="0">
        <stop offset="0" stop-color="var(--paper)"/>
        <stop offset="1" stop-color="var(--paper-shade)"/>
      </linearGradient>
      <linearGradient id="goldBand" x1="0" y1="1" x2="1" y2="0">
        <stop offset="0" stop-color="var(--gold-dark)"/>
        <stop offset=".45" stop-color="var(--gold)"/>
        <stop offset=".75" stop-color="var(--gold-light)"/>
        <stop offset="1" stop-color="var(--gold)"/>
      </linearGradient>
      <linearGradient id="bathroomTones" x1="0" y1="0" x2="0" y2="1">
        <stop offset="0" stop-color="#ede6c9"/>
        <stop offset=".55" stop-color="#d9cfae"/>
        <stop offset="1" stop-color="#8f7d62"/>
      </linearGradient>
      <linearGradient id="interiorTones" x1="0" y1="0" x2="1" y2="1">
        <stop offset="0" stop-color="#c8d3de"/>
        <stop offset="1" stop-color="#4d5560"/>
      </linearGradient>
    </defs>

    <rect class="panel-back" x="0" y="0" width="560" height="792" fill="url(#paperLeft)"/>
    <rect class="panel-cover" x="560" y="0" width="560" height="792" fill="var(--paper)"/>

    <path class="gold-sweep" fill="url(#goldBand)"
      d="M1120,86 C900,80 715,128 612,250 C530,348 470,470 360,530 C240,595 120,615 0,622 L0,792 L1120,792 Z"/>

    <path class="cover-photo" role="img" aria-label="Photo of a bright luxury bathroom with a built-in tub, wooden dresser and polished stone floor"
      fill="url(#bathroomTones)"
      d="M1120,104 C905,100 728,146 628,262 C548,356 492,478 400,552 L1120,552 Z"/>

    <path class="blue-edge" fill="none" stroke="var(--blue-line)" stroke-width="3"
      d="M0,662 C120,594 280,554 440,542 C650,526 900,529 1120,539"/>
    <path class="dark-base" fill="var(--ink)"
      d="M0,668 C120,600 280,560 440,548 C650,532 900,535 1120,545 L1120,792 L0,792 Z"/>

    <circle class="inset-ring" cx="330" cy="556" r="84" fill="url(#goldBand)"/>
    <circle class="inset-photo" cx="330" cy="556" r="74" fill="url(#interiorTones)" role="img" aria-label="Photo of a modern living room interior with a staircase and curtains"/>

    <line class="fold" x1="560" y1="0" x2="560" y2="792" stroke="rgba(0,0,0,.08)" stroke-width="2"/>
  </svg>

  <div class="brand-name cover-brand">DORVIKA</div>
  <div class="cover-web">www.dorvika.ae</div>
  <h1 class="cover-headline">Get a free quote today!</h1>
  <p class="cover-body">We believe in quality beginnings and flawless finishes. We are a team of creative designers and constructors with years of experience and expertise in providing complete interior design and construction services. Our unique designing prowess is complemented by our unflinching commitment to quality construction. Our team specializes in classic and contemporary high quality construction in Dubai for commercial and residential projects.</p>

  <div class="brand-name back-brand">DORVIKA</div>
  <div class="back-phone">800 – DORVIKA</div>
  <div class="back-quote">Quality is not an act, it is a habit – Theron Vale</div>
  <div class="back-email">CONTACT@DORVIKA.AE</div>
  <div class="back-address">Dorvika LLC, Marlow Point Building, Office 1207, Business Bay, Dubai</div>
</main>
</body>
</html>
```